New Payments Start-up requires Logo, Style Guide and Web Site Design

We need a logo, style guide (colour templates etc.) and marketing web-site (HTML/CSS styling) for Fenwu, a new account-to-account payment product for use in the Single European Payment Area (SEPA).

The design is for the product only, not a company brand. We're looking for basic palette and style guidelines also. The web site need only be a basic responsive cross-platform design and layout. We will produce our own content.

We have no requirements for specific colours or logo styles. It is a financial product, however, so should not appear too quirky or untrustworthy.

The product is still in the early phases of development, so we're not able to provide pictures or other content.

As a little more detail on how things work, though, our end customers will arrive at our site through redirection from our merchant partners (a number of whom are large multi-national companies) who have offered our services as an alternative to credit card payments. They will be able to set up a SEPA direct debit mandate online in just a few pages, secure that with a password and use it to pay both immediately and in future with a simple confirmation of the password… a quick, easy checkout.

Because we work with large customer in the payments space, whilst we’d like the brand to be modern and appealing, it has to engender trust and stability. Whilst this product is new and in start-up phase, our company has been in alternative payments for nearly 10 years and have strong products in Europe in the Pre-Paid Zelo/TrevinCard and Voucher space. We'd like to treat this separately, however, which is why we've briefed accordingly.

Reason: Apologies for the extension, but I had a couple of designers contact me to say they had completed work but were unable to submit because time ran out. I'll only extend this once, though, because we need to get cracking on the project. Many thanks Jem

Target Market(s)

European alternative payment customers

Industry/Entity Type

Financial

Logo Text

fenwu

Coding

Coded - Design and coding required

Number of Pages Required

1 page

Font styles to use
Sans Serif

```html
<!DOCTYPE html>
<html lang="en">
<head>
<meta charset="utf-8">
<title>Fenwu – SEPA account-to-account payments</title>
<link rel="stylesheet" href="https://fonts.googleapis.com/css2?family=Oswald:wght@300;400;500&family=Roboto:wght@300;400;500&display=swap">
<style>
:root{
  --blue:#1a86c8;
  --blue-deep:#0b7cc4;
  --teal:#3cc2b4;
  --ink:#222;
  --text:#555;
  --muted:#6a6a6a;
  --light:#f1f1f2;
  --white:#fff;
  --dark:#121212;
  --circle:#3e8fc0;
}
*{box-sizing:border-box;margin:0;padding:0}
html,body{width:1200px;height:2258px;overflow:hidden}
body{position:relative;background:var(--white);font-family:'Roboto',sans-serif;color:var(--text)}

/* header */
.site-header{position:absolute;left:0;top:0;width:1200px;height:113px;background:var(--white)}
.brand{position:absolute;left:89px;top:36px;font-family:'Oswald',sans-serif;font-weight:500;font-size:42px;line-height:1;color:var(--blue)}
.main-nav{position:absolute;top:53px;left:483px;font-size:15.5px;color:#333}
.main-nav a{text-decoration:none;color:inherit;position:absolute;white-space:nowrap}
.main-nav a.is-active{color:var(--blue)}

/* hero */
.hero{position:absolute;left:0;top:113px;width:1200px;height:534px;
  background:linear-gradient(100deg,#6e7c70 0%,#8a9aa6 25%,#5c86a8 48%,#2f4f72 72%,#1f3451 100%)}
.hero-shade{position:absolute;inset:0;background:rgba(20,30,45,.28)}
.hero-kicker{position:absolute;left:0;width:1200px;top:226px;text-align:center;font-family:'Oswald',sans-serif;font-weight:300;font-size:33px;color:var(--white)}
.hero-title{position:absolute;left:0;width:1200px;top:282px;text-align:center;font-family:'Oswald',sans-serif;font-weight:500;font-size:44px;letter-spacing:-.3px;color:var(--white)}
.hero-arrow{position:absolute;top:262px;width:36px;height:36px;border-radius:50%;background:rgba(40,40,40,.55)}
.hero-arrow svg{position:absolute;left:11px;top:10px}

/* welcome */
.welcome-title{position:absolute;top:700px;left:0;width:1200px;text-align:center;font-size:29px;font-weight:400;color:var(--ink)}
.welcome-title span{color:var(--blue)}
.welcome-copy{position:absolute;left:100px;width:1000px;top:757px;text-align:center;font-size:13.1px;line-height:22.6px;color:var(--muted)}

/* split promo */
.promo{position:absolute;top:884px;height:269px;color:var(--white)}
.promo--how{left:0;width:592px;background:linear-gradient(90deg,#1d93d2,#2a9fd9 60%,#1a8bcc)}
.promo--product{left:592px;width:608px;background:linear-gradient(90deg,#2db7b5,#45c6b9 55%,#36bcb0)}
.promo h2{position:absolute;top:50px;font-size:21px;font-weight:500;text-transform:uppercase;white-space:nowrap}
.promo p{position:absolute;top:86px;width:452px;font-size:12.1px;line-height:21.6px}
.btn{position:absolute;top:194px;width:93px;height:34px;border-radius:3px;background:linear-gradient(#fafafa,#dcdcdc);border:1px solid #bbb;color:#333;font-size:12.5px;line-height:32px;text-align:center;box-shadow:0 1px 2px rgba(0,0,0,.25)}

/* features */
.features{position:absolute;left:0;top:1153px;width:1200px;height:328px;background:var(--light)}
.feature{position:absolute;top:76px;width:300px;text-align:center}
.feature-icon{position:relative;margin:0 auto;width:100px;height:100px;border-radius:50%;background:var(--circle);border:4px solid #dfe3e6;box-shadow:0 0 0 1px #c9d0d5}
.feature-icon svg{position:absolute;left:50%;top:50%;transform:translate(-50%,-50%)}
.feature h3{margin-top:20px;font-size:18px;font-weight:500;color:#1163a6}
.feature p{margin:6px auto 0;width:244px;font-size:11.5px;line-height:18px;color:#444}

/* move money */
.money-photo{position:absolute;left:89px;top:1552px;width:442px;height:262px;border:4px solid var(--white);box-shadow:0 0 4px rgba(0,0,0,.3);
  background:linear-gradient(120deg,#c9d4e2 0%,#eef0f3 35%,#f4e2d6 60%,#dad4cf 100%)}
.money-title{position:absolute;left:560px;top:1552px;font-size:19.5px;font-weight:500;color:#1a7fc0;text-transform:uppercase}
.money-copy{position:absolute;left:560px;top:1587px;width:552px;font-size:13.4px;line-height:24px;color:var(--text)}
.money-sub{position:absolute;left:560px;top:1685px;font-size:14.5px;color:var(--blue)}
.money-steps{position:absolute;left:560px;top:1716px;list-style:none;font-size:13.4px;line-height:24px;color:var(--text)}
.money-steps li::before{content:"»";margin-right:8px;color:#666}

/* partners */
.partner{position:absolute;top:1895px;font-size:22px;font-weight:500;color:#444;display:flex;align-items:center;gap:8px;white-space:nowrap}
.partner i{display:block;width:22px;height:22px;border-radius:50%;background:#555}

/* footer */
.site-footer{position:absolute;left:0;top:1957px;width:1200px;height:220px;background:var(--blue-deep);color:var(--white)}
.footer-col{position:absolute;top:36px}
.footer-col h4{font-size:15.5px;font-weight:400;text-transform:uppercase;margin-bottom:18px}
.footer-links{list-style:none;font-size:11.5px;line-height:24.5px}
.footer-links li::before{content:"";display:inline-block;width:0;height:0;border-left:4px solid var(--white);border-top:3.5px solid transparent;border-bottom:3.5px solid transparent;margin-right:8px;vertical-align:1px}
.footer-col p{font-size:10.8px;line-height:16.5px}
.contact p{margin-bottom:13px;line-height:20px;font-size:11.3px}
.news-note{width:205px}
.news-form{display:flex;margin-top:14px}
.news-form span{width:145px;height:31px;background:#eef0f2;color:#555;font-size:11px;line-height:31px;padding-left:14px}
.news-form b{width:57px;height:31px;background:#111;color:#fff;font-weight:400;font-size:12px;line-height:31px;text-align:center}
.socials{display:flex;gap:12px;margin-top:14px}
.socials i{width:33px;height:33px;border-radius:50%;border:1px solid rgba(255,255,255,.7)}
.copyright{position:absolute;left:0;top:2177px;width:1200px;height:81px;background:var(--dark);color:var(--white);text-align:center;font-size:12px;line-height:81px}
</style>
</head>
<body>

<header class="site-header">
  <div class="brand">Fenwu</div>
  <nav class="main-nav">
    <a class="is-active" style="left:0">HOME</a>
    <a style="left:80px">ABOUT US</a>
    <a style="left:188px">SERVICES</a>
    <a style="left:290px">PROJECT</a>
    <a style="left:394px">BLOG</a>
    <a style="left:473px">NEWS</a>
    <a style="left:552px">CONTACTS</a>
  </nav>
</header>

<section class="hero" role="img" aria-label="Photo of three colleagues working together at a laptop in a bright office">
  <div class="hero-shade"></div>
  <div class="hero-kicker">New account-to-account payment productfor use in the</div>
  <div class="hero-title">SINGLE EUROPEAN PAYMENT AREA (SEPA)</div>
  <div class="hero-arrow" style="left:39px"><svg width="14" height="16" viewBox="0 0 14 16"><path d="M10 2 4 8l6 6" fill="none" stroke="#fff" stroke-width="2.4"/></svg></div>
  <div class="hero-arrow" style="left:1120px"><svg width="14" height="16" viewBox="0 0 14 16"><path d="M4 2l6 6-6 6" fill="none" stroke="#fff" stroke-width="2.4"/></svg></div>
</section>

<h1 class="welcome-title">WELCOME TO <span>FENWU</span></h1>
<p class="welcome-copy">As a little more detail on how things work, though, our end customers will arrive at our site through redirection from our merchant partners (a number of whom are large multi- national companies) who have offered our services as an alternative to credit card payments. They will be able to set up a SEPA direct debit mandate online in just a few pages, secure that with a password and use it to pay both immediately and in future with a simple confirmation of the password... a quick, easy checkout.</p>

<section class="promo promo--how" role="img" aria-label="Blue-tinted photo of a smiling woman in an office">
  <h2 style="left:89px">How it work</h2>
  <p style="left:89px">&nbsp;Lorem Ipsum has been the industry's standard dummy text ever since the 1500s, when an unknown printer took a galley of type and scrambled it to make a type specimen book. It has survived not only five centuries, but also the leap into elec- tronic typesetting, remaining essentially unchanged. It was popularised</p>
  <div class="btn" style="left:89px">Read More</div>
</section>
<section class="promo promo--product" role="img" aria-label="Teal-tinted photo of a hand holding a phone">
  <h2 style="left:61px">Account-to-account payment product</h2>
  <p style="left:59px">&nbsp;Lorem Ipsum has been the industry's standard dummy text ever since the 1500s, when an unknown printer took a galley of type and scrambled it to make a type specimen book. It has survived not only five centuries, but also the leap into elec- tronic typesetting, remaining essentially unchanged. It was popularised</p>
  <div class="btn" style="left:60px">Read More</div>
</section>

<section class="features">
  <div class="feature" style="left:88px">
    <div class="feature-icon"><svg width="40" height="36" viewBox="0 0 40 36"><rect x="2" y="3" width="36" height="23" rx="2" fill="#fff"/><rect x="6" y="7" width="28" height="15" fill="var(--circle)"/><rect x="16" y="26" width="8" height="5" fill="#fff"/><rect x="11" y="31" width="18" height="3" fill="#fff"/></svg></div>
    <h3>PASSWORD</h3>
    <p>Lorem Ipsum has been the industry's standard dummy text ever since the 1500s, when an unknown printer took a galley</p>
  </div>
  <div class="feature" style="left:424px">
    <div class="feature-icon"><svg width="38" height="36" viewBox="0 0 38 36"><path d="M36 2 2 17l11 4 3 12 6-8 9 6z" fill="#fff"/><path d="M36 2 13 21" stroke="var(--circle)" stroke-width="2"/></svg></div>
    <h3>QUICK</h3>
    <p>Lorem Ipsum has been the industry's standard dummy text ever since the 1500s, when an unknown printer took a galley</p>
  </div>
  <div class="feature" style="left:761px">
    <div class="feature-icon"><svg width="36" height="40" viewBox="0 0 36 40"><rect x="4" y="2" width="18" height="24" fill="#fff"/><path d="M12 10h14l8 8v20H12z" fill="#fff" stroke="var(--circle)" stroke-width="2"/><path d="M26 10v8h8" fill="none" stroke="var(--circle)" stroke-width="2"/></svg></div>
    <h3>CHECKOUT</h3>
    <p>Lorem Ipsum has been the industry's standard dummy text ever since the 1500s, when an unknown printer took a galley</p>
  </div>
</section>

<div class="money-photo" role="img" aria-label="Photo of a smiling woman relaxing on a sofa with a laptop"></div>
<h2 class="money-title">Move money between accounts</h2>
<p class="money-copy">Account-to-Account payments allow you to easily move money between accounts, both inter- nally and externally. This feature gives you greater control when moving funds from Harlow Federal® to outside institutions, and saves money on wire transfers. Internal payments, from one Harlow Federal account to another, do not incur a service charge.</p>
<div class="money-sub">To move money :</div>
<ul class="money-steps">
  <li>&nbsp;Log in to Clearline Online® banking</li>
  <li>Select the Payments tab</li>
  <li>Select the Acct-to-Acct sub tab</li>
  <li>Follow instructions on the screen</li>
</ul>

<div class="partner" style="left:113px"><i></i>Tarbrook</div>
<div class="partner" style="left:318px"><i></i>Velcourt</div>
<div class="partner" style="left:518px"><i></i>Ossington</div>
<div class="partner" style="left:729px"><i></i>Brimley</div>
<div class="partner" style="left:934px"><i></i>Haldane</div>

<footer class="site-footer">
  <div class="footer-col" style="left:89px">
    <h4>Links</h4>
    <ul class="footer-links">
      <li>Customer Support</li>
      <li>Documentation</li>
      <li>Resources</li>
      <li>General FAQs</li>
      <li>Shortcodes</li>
    </ul>
  </div>
  <div class="footer-col" style="left:300px;width:232px">
    <h4>Payment product</h4>
    <p style="text-align:justify">&nbsp;Lorem Ipsum has been the industry's standard dummy text ever since the 1500s, when an unknown printer took a</p>
    <p style="text-align:justify;margin-top:8px">a galley of type and scrambled it to make a type specimen book. It has survived not only five cen- turies, but also the leap into electronic typeset-</p>
  </div>
  <div class="footer-col contact" style="left:650px">
    <h4>Get in touch</h4>
    <p>Address : 12 Linden Row Ave,<br>Marlow Park, NJ</p>
    <p>Phone : 201 555 0147</p>
    <p>Email : info@samplemail.test</p>
  </div>
  <div class="footer-col" style="left:907px;width:210px">
    <h4>Newsletter</h4>
    <p class="news-note">Your about us information would fit here nicely.</p>
    <div class="news-form"><span>Email address</span><b>Submit</b></div>
    <div class="socials"><i></i><i></i><i></i></div>
  </div>
</footer>

<div class="copyright">Copyright © 2016. All Rights Reserved</div>

</body>
</html>
```